4D Cradle Glimpse Luxury Ultrasound Billboard

Design a HIGH-END, MODERN billboard for my private prenatal ultrasound studio, 4D Cradle Glimpse, located in Pace, Florida.
This billboard will be viewed by drivers traveling at highway speeds, so it must be extremely clean, simple, and readable within 6 seconds.
About My Business
4D Cradle Glimpse is a private prenatal ultrasound studio specializing in:
Highest technology 4D/HD Ultrasounds
Early Gender Determination
Pregnancy Confirmation
I have been serving families for nearly 10 years and is known for creating a memorable experience, not just an ultrasound appointment.
Design Style
I DO NOT want:
Flowers
Leaves
Swirls
Glitter
Hearts everywhere
Busy backgrounds
Generic maternity stock graphics
I DO want:
Modern
Luxury
Upscale
Clean
Professional
Eye-catching
Premium medical spa feel
Colors
Use colors from my logo:
LOGO Green ( or a deep green)
Black
White
Soft Gold accents
Images:
Incorporate my professional headshot in a clean, modern way, logo, and the ultrasound images
Text
Keep wording minimal.
Primary Headline ( OPEN TO IDEAS) :
EXAMPLES ( WOULD RATHER SOMETHING MORE CATCHY)
" ADVANCED IMAGING. UNFORGETTABLE MOMENTS"
"MEET YOUR BABY BEFORE BIRTH"
Under headline:
4D Ultrasound • Early Gender • Pregnancy Confirmation
Business Name:
4D Cradle Glimpse
Private Prenatal Ultrasound Studio
Phone Number:
850-471-5923
Important
This billboard must be readable in 5–6 seconds from a moving vehicle.
Less text is better.
The phone number and business name must be visible from a distance.
The design should feel like a premium brand that immediately tells expecting parents:
“This is where I go to see my baby.”
Files Provided
Official logo
Headshot
Ultrasound images
Don’t make this look like a medical office billboard.
Make it look like a luxury baby experience billboard. That’s what separates 4D Cradle Glimpse from hospitals, OB offices, and all the new studios popping up around you. The emotional connection is what gets moms to book. ❤️
Billboard Size - 10.6” x 36”

```html
<!DOCTYPE html>
<html lang="en">
<head>
<meta charset="utf-8">
<title>4D Cradle Glimpse Billboard</title>
<link href="https://fonts.googleapis.com/css2?family=Playfair+Display:wght@700;800&family=Kaushan+Script&family=Roboto+Condensed:wght@500;700&family=Roboto:wght@500&display=swap" rel="stylesheet">
<style>
  :root {
    --backdrop: #7a828b;
    --cream: #fbf6ee;
    --cream-deep: #f4e6cc;
    --green: #173a2b;
    --gold: #cf9a2c;
    --gold-soft: #f3dfb8;
    --frame-grey: #6f7c78;
    --white: #ffffff;
    --scan-dark: #2a140a;
    --scan-mid: #b8622e;
    --scan-light: #e39a62;
    --photo-tone: #c9b39a;
  }
  * { margin: 0; padding: 0; box-sizing: border-box; }
  html, body { width: 1145px; height: 1200px; overflow: hidden; }
  body { background: var(--backdrop); position: relative; }

  .billboard {
    position: absolute; left: 30px; top: 432px;
    width: 1085px; height: 335px;
    background: linear-gradient(90deg, var(--cream) 0%, #fdf9f3 60%, var(--cream) 100%);
    overflow: hidden;
    box-shadow: 0 6px 14px rgba(0,0,0,0.25);
  }
  .bg-curves { position: absolute; inset: 0; }

  .ultrasound-frame {
    position: absolute; left: -100px; top: -40px;
    width: 380px; height: 415px; border-radius: 50%;
    border: 3px solid var(--gold);
    background: radial-gradient(ellipse at 55% 45%, var(--scan-light) 0%, var(--scan-mid) 45%, var(--scan-dark) 100%);
  }

  .headline { position: absolute; left: 300px; width: 485px; text-align: center; color: var(--green); }
  .headline-kicker {
    top: 2px; font-family: "Playfair Display", serif; font-weight: 700;
    font-size: 46px; letter-spacing: 2px; display: flex; align-items: center; justify-content: center; gap: 12px;
  }
  .headline-kicker::before, .headline-kicker::after {
    content: ""; width: 52px; height: 2px; background: var(--gold);
  }
  .headline-main {
    top: 42px; font-family: "Playfair Display", serif; font-weight: 800;
    font-size: 136px; line-height: 1; letter-spacing: 6px;
  }
  .headline-script {
    top: 140px; font-family: "Kaushan Script", cursive; color: var(--gold);
    font-size: 74px; line-height: 1.1;
  }
  .script-underline { position: absolute; left: 590px; top: 232px; }

  .services {
    position: absolute; left: 300px; width: 485px; top: 249px;
    text-align: center; font-family: "Roboto Condensed", sans-serif; font-weight: 500;
    font-size: 17px; color: var(--green);
  }
  .services .dot { color: var(--gold); margin: 0 10px; }

  .phone-pill {
    position: absolute; left: 306px; top: 268px; width: 429px; height: 60px;
    background: var(--green); border-radius: 30px;
    display: flex; align-items: center;
  }
  .phone-icon {
    width: 60px; height: 60px; border-radius: 50%;
    background: var(--white); border: 4px solid var(--green);
    display: flex; align-items: center; justify-content: center;
  }
  .phone-number {
    flex: 1; text-align: center; padding-right: 12px;
    font-family: "Roboto Condensed", sans-serif; font-weight: 700;
    font-size: 48px; color: var(--white); letter-spacing: 0.5px;
  }

  .headshot {
    position: absolute; left: 850px; top: 6px; width: 182px; height: 210px;
    border-radius: 90px 90px 0 0;
    background: linear-gradient(180deg, #e2d1b8 0%, var(--photo-tone) 55%, var(--green) 100%);
  }

  .brand-card {
    position: absolute; left: 833px; top: 206px; width: 236px; height: 122px;
    background: var(--white); border: 2px solid var(--frame-grey); border-radius: 16px;
    display: flex; flex-direction: column; align-items: center; justify-content: center; gap: 8px;
  }
  .brand-name {
    font-family: "Playfair Display", serif; font-weight: 700;
    font-size: 26px; color: var(--green); text-align: center; line-height: 1.1;
  }
  .brand-tagline {
    font-family: "Roboto", sans-serif; font-weight: 500; font-size: 11px;
    letter-spacing: 0.6px; color: var(--green); border-top: 1px solid var(--gold); padding-top: 6px;
  }
</style>
</head>
<body>
  <section class="billboard">
    <svg class="bg-curves" width="1085" height="335" viewBox="0 0 1085 335" aria-hidden="true">
      <path d="M700 335 C 860 250, 950 120, 1085 60 L1085 335 Z" fill="var(--gold-soft)" opacity="0.55"/>
      <path d="M780 335 C 900 280, 990 190, 1085 150 L1085 335 Z" fill="var(--cream-deep)" opacity="0.8"/>
      <path d="M880 0 C 960 40, 1040 60, 1085 110" stroke="var(--gold-soft)" stroke-width="22" fill="none" opacity="0.6"/>
    </svg>

    <div class="ultrasound-frame" role="img" aria-label="4D ultrasound image of twin babies face to face"></div>

    <h1>
      <span class="headline headline-kicker">MEET YOUR</span>
      <span class="headline headline-main">BABY</span>
      <span class="headline headline-script">Before Birth</span>
    </h1>
    <svg class="script-underline" width="110" height="14" viewBox="0 0 110 14" aria-hidden="true">
      <path d="M2 12 C 40 2, 80 2, 108 4" stroke="var(--gold)" stroke-width="3" fill="none" stroke-linecap="round"/>
    </svg>

    <p class="services">4D Ultrasound<span class="dot">•</span>Early Gender<span class="dot">•</span>Pregnancy Confirmation</p>

    <div class="phone-pill">
      <span class="phone-icon">
        <svg width="30" height="30" viewBox="0 0 24 24" aria-hidden="true">
          <path fill="var(--green)" d="M6.6 10.8c1.4 2.8 3.8 5.1 6.6 6.6l2.2-2.2c.3-.3.7-.4 1-.2 1.1.4 2.3.6 3.6.6.6 0 1 .4 1 1V20c0 .6-.4 1-1 1C10.6 21 3 13.4 3 4c0-.6.4-1 1-1h3.5c.6 0 1 .4 1 1 0 1.3.2 2.5.6 3.6.1.3 0 .7-.2 1l-2.3 2.2z"/>
        </svg>
      </span>
      <span class="phone-number">850-471-5923</span>
    </div>

    <div class="headshot" role="img" aria-label="Professional headshot of the studio owner in green scrubs"></div>

    <div class="brand-card">
      <span class="brand-name">4D Cradle Glimpse</span>
      <span class="brand-tagline">PRENATAL ULTRASOUND STUDIO</span>
    </div>
  </section>
</body>
</html>
```